Business Card Design Project : Ridgeline Press

In preparation for market launch, Tamarind's Ridgeline Press require the development of a business card. Ridgeline Press is a Community online publishing web portal. We provide the the city of Whistler located in B.C. (Canada) business directories, News, Classified ads, News, Events and blogs etc.

The main focus of the brand is to help local businesses to corporate with their online advertisement and marketing. Meeting our clients face to face is a must (B2B).

Target Market(s)

The target market is B2B customers. Business Owners to Marketing, advertising Managers

Industry/Entity Type

Business

Requirements
Must have
• - The business card will be two sided.
the BACK side will have our logo which consist of (icon, url,slogan) submited. The logo will be middle and centred.

The FRONT side should have company details:

Company Legal Name: TAMARIND RIDGELINE MEDIA

Owen Farsk
Director of Sales & Marketing

www.tamarindridgeline.biz
owen@tamarindridgeline.biz

Phone: 604 317 8842
#2714 - 582 E. Halvern St.
Vancouver, B.C. V7K2R4 Canada
Nice to have
• - For the "FRONT" side of our business card. You can separate or re-arrange with our logo components (icon, logo,slogan). It does not have to be together.

Also our company legal name is rather long so arrange or organize the name in a way to make it shorter. Your experience and creativity will have to come in play.
Should not have
• should not have other colors beside logo color and black text (2 colors). Also nothing Three dimensional

```html
<!DOCTYPE html>
<html lang="en">
<head>
<meta charset="utf-8">
<title>Ridgeline Press – Business Card</title>
<link rel="stylesheet" href="https://fonts.googleapis.com/css2?family=Source+Sans+3:wght@400;600&display=swap">
<style>
  :root {
    --backdrop: #1c1c1c;
    --card: #ffffff;
    --brand-blue: #2a8bd4;
    --ink: #111111;
    --ink-soft: #555555;
    --name-grey: #7a7a7a;
    --faint-grey: #d9d9d9;
    --frame-grey: #9a9a9a;
    --rule-grey: #e2e2e2;
  }
  html, body {
    margin: 0;
    width: 1200px;
    height: 848px;
    overflow: hidden;
    background: var(--backdrop);
    font-family: "Source Sans 3", "Myriad Pro", sans-serif;
  }
  .canvas { position: relative; width: 1200px; height: 848px; }
  .card {
    position: absolute;
    background: var(--card);
    box-shadow: 0 6px 18px rgba(0,0,0,.45);
  }
  .card__frame {
    position: absolute;
    left: 6px; top: 6px;
    width: 170px; height: 150px;
    border-top: 3px solid var(--frame-grey);
    border-left: 3px solid var(--frame-grey);
    border-top-left-radius: 6px;
    -webkit-mask-image: linear-gradient(135deg, #000 20%, transparent 80%);
            mask-image: linear-gradient(135deg, #000 20%, transparent 80%);
  }

  /* Back side */
  .card--back { left: 130px; top: 90px; width: 490px; height: 318px; }
  .back__brand {
    position: absolute; left: 0; right: 0; top: 100px;
    text-align: center;
    font-size: 42px; font-weight: 600; color: var(--brand-blue);
    letter-spacing: .5px;
  }
  .back__url {
    position: absolute; left: 0; right: 0; top: 178px;
    text-align: center;
    font-size: 26px; font-weight: 400; color: var(--ink);
  }
  .back__slogan {
    position: absolute; left: 0; right: 0; top: 207px;
    text-align: center;
    font-size: 19px; color: var(--brand-blue);
  }

  /* Front side */
  .card--front { left: 405px; top: 345px; width: 605px; height: 395px; }
  .front__divider { position: absolute; inset: 0; }
  .contact {
    position: absolute; left: 23px; top: 104px; width: 260px;
  }
  .contact__name {
    margin: 0;
    font-size: 52px; font-weight: 400; line-height: 1;
    background: linear-gradient(90deg, #555 0%, #aaa 100%);
    -webkit-background-clip: text; background-clip: text; color: transparent;
    white-space: nowrap;
  }
  .contact__details { margin-left: 10px; text-align: center; width: 230px; }
  .contact__title { margin-top: 12px; font-size: 17px; color: var(--ink); white-space: nowrap; }
  .contact__email { margin-top: 3px; font-size: 10px; color: var(--brand-blue); }
  .contact__web { font-size: 10px; color: var(--ink); }
  .contact__phone { margin-top: 12px; font-size: 15px; color: var(--ink); }
  .address {
    position: absolute; left: 23px; bottom: 14px;
    font-size: 14px; color: var(--ink-soft); white-space: nowrap;
  }
  .address__city { color: var(--brand-blue); }
  .company {
    position: absolute; left: 345px; top: 162px; width: 245px;
    text-align: center;
    font-weight: 600; color: var(--faint-grey); line-height: 1;
  }
  .company__line { font-size: 30px; letter-spacing: .5px; }
  .company__slogan {
    margin-top: 12px;
    font-size: 13px; font-weight: 400; color: var(--brand-blue);
  }
</style>
</head>
<body>
<main class="canvas">

  <section class="card card--back" aria-label="Card back">
    <div class="card__frame"></div>
    <div class="back__brand">Ridgeline Press</div>
    <div class="back__url">www.tamarindridgeline.biz</div>
    <div class="back__slogan">Your information gateway</div>
  </section>

  <section class="card card--front" aria-label="Card front">
    <div class="card__frame"></div>
    <svg class="front__divider" width="605" height="395" viewBox="0 0 605 395" aria-hidden="true">
      <line x1="400" y1="30" x2="200" y2="345" stroke="var(--rule-grey)" stroke-width="1"/>
    </svg>

    <div class="contact">
      <h1 class="contact__name">Owen Farsk</h1>
      <div class="contact__details">
        <div class="contact__title">Director of Sales &amp; Marketing</div>
        <div class="contact__email">owen@tamarindridgeline.biz</div>
        <div class="contact__web">www.tamarindridgeline.biz</div>
        <div class="contact__phone">Phone: 604 317 8842</div>
      </div>
    </div>

    <div class="company">
      <div class="company__line">TAMARIND</div>
      <div class="company__line">RIDGELINE MEDIA</div>
      <div class="company__slogan">Your information gateway</div>
    </div>

    <div class="address">#2714 - 582 E. Halvern St. <span class="address__city">Vancouver, B.C. V7K2R4 Canada</span></div>
  </section>

</main>
</body>
</html>
```